My name is Delia Okonkwo,I want to create a web page for my personal dog grooming business. The name on the web page can be "Delia's Dog Grooming" I am located in San Antonio Texas. The page would help grow my customer base. Before and after pictures would display the quality of work that I do. On my page I can provide information about myself, my services, and pricing.
Updates

I have updated project to guaranteed pay

Please try to incorporate a schnauzer in an icon or logo. My dog is a schnauzer. THANKS!!!!!!!!!!!!

Target Market(s)

Dog Owners

Industry/Entity Type

Business

Requirements
Must have
• -A spot for before and after pictures.
-An about me section
-A section to make an appointment
Nice to have
• My favorite Color is purple. I think different shades of purple would be nice or purple with a light green

please incorporate a schnauzer in any icon or logo. My dog is a schnauzer.

```html
<!DOCTYPE html>
<html lang="en">
<head>
<meta charset="utf-8">
<title>Delia's Dog Grooming</title>
<link href="https://fonts.googleapis.com/css2?family=Ubuntu:wght@400;500;700&family=Arimo:wght@400;700&display=swap" rel="stylesheet">
<style>
:root{
  --purple-deep:#3e0840;
  --purple:#5a0a5c;
  --purple-mid:#7a1a7c;
  --purple-bright:#8e2290;
  --green-light:#c4e01a;
  --green:#86c41a;
  --white:#ffffff;
  --grey-line:#c9c9c9;
  --grey-text:#8a8a8a;
  --body-text:#4a4a4a;
  --red-link:#c4121a;
}
*{box-sizing:border-box;margin:0;padding:0}
html,body{width:954px;height:1200px;overflow:hidden}
body{font-family:"Arimo",Arial,sans-serif;background:linear-gradient(180deg,var(--purple-deep) 0%,#6a1470 45%,var(--purple-bright) 100%);position:relative}
.canvas{position:absolute;inset:0;width:954px;height:1200px}
.page{position:absolute;left:58px;top:16px;width:837px;height:1106px;background:var(--white);border-radius:4px}
.abs{position:absolute}
/* header */
.brand{left:62px;top:18px;width:304px;height:277px;background:linear-gradient(180deg,var(--green-light),var(--green));display:flex;align-items:center;justify-content:center;flex-direction:column;gap:4px}
.brand-name{font-family:"Ubuntu",sans-serif;font-weight:700;font-size:32px;line-height:1.15;color:var(--purple);text-align:center}
.hero{left:368px;top:18px;width:525px;height:277px;background:linear-gradient(135deg,#5f7a3a 0%,#8f8e86 45%,#a9a79f 70%,#6d6a62 100%)}
.hero-caption{left:368px;top:250px;width:525px;height:45px;background:rgba(40,40,40,.55);color:#fff;font-family:"Ubuntu",sans-serif;font-size:13.5px;line-height:21px;padding:2px 0 0 84px}
.hero-arrow{width:24px;height:24px;border-radius:50%;background:#1c1c1c;border:2px solid #fff}
.hero-arrow svg{display:block;margin:5px auto 0}
/* nav */
.nav{left:58px;top:297px;width:837px;height:44px;background:linear-gradient(180deg,#fff,#f1f1f1);border-bottom:1px solid #e4e4e4}
.nav-item{position:absolute;top:0;height:41px;line-height:41px;font-size:11.5px;color:var(--purple);text-transform:uppercase}
.nav-item.active{background:var(--purple);color:#fff;border-radius:3px;text-align:center}
/* side panels */
.panel{border:1px solid #dcdcdc;border-radius:12px;background:#fff}
.panel-head{background:linear-gradient(180deg,var(--purple-mid),var(--purple));color:#fff;font-family:"Ubuntu",sans-serif;font-size:15px;border-radius:10px;display:flex;align-items:center}
.field{left:91px;width:199px;height:31px;border:1px solid #bdbdbd;border-radius:4px;background:linear-gradient(180deg,#fff,#f6f6f6);font-size:11px;color:var(--grey-text);line-height:29px;padding-left:22px}
.field.select{padding-left:15px}
.field.select svg{position:absolute;right:10px;top:11px}
.submit{left:216px;top:695px;width:70px;height:26px;background:var(--purple);color:#fff;font-size:11.5px;border-radius:3px;text-align:center;line-height:26px}
.video{left:79px;top:746px;width:225px;height:181px;background:linear-gradient(135deg,#d9d9d9 0%,#6e6e6e 40%,#1f1f1f 75%,#0b0b0b 100%);border-radius:4px}
.video-title{left:80px;top:746px;font-size:6.5px;color:#fff;font-weight:700}
.play{left:174px;top:818px;width:34px;height:24px;background:#1a1a1a;border:1px solid #ddd;border-radius:4px}
.services-list{left:97px;top:1001px;list-style:none;font-size:11px;color:#333}
.services-list li{height:20.5px;display:flex;align-items:center;gap:8px}
/* main */
.heading{font-family:"Ubuntu",sans-serif;font-size:19px;color:#333}
.heading b{font-weight:400;color:var(--purple)}
.portrait{left:349px;top:413px;width:119px;height:186px;background:linear-gradient(180deg,#3a2a22 0%,#2a2a2a 45%,#1a1a1a 100%);border-radius:40px 40px 6px 6px}
.about-text{left:503px;top:420px;width:345px;font-size:11.3px;line-height:18.5px;color:var(--body-text)}
.read-more{left:779px;top:582px;font-size:11px;color:var(--red-link)}
.showcase{background:var(--purple);border-radius:3px}
.shot{border:1px solid #fff;border-radius:4px}
.label{font-size:13.5px;color:#fff;width:226px;text-align:center}
/* footer */
.social{top:1146px;width:26px;height:26px;border-radius:50%;background:linear-gradient(180deg,#fff,#cfd8ea)}
.social-name{top:1174px;width:40px;text-align:center;font-size:7.5px;color:#fff}
.footer-links{left:444px;top:1144px;font-size:10px;color:#fff;word-spacing:1px}
.footer-links span{margin:0 9px}
.copyright{left:529px;top:1175px;font-size:11px;color:#fff}
</style>
</head>
<body>
<div class="canvas">
  <div class="page"></div>

  <header>
    <div class="abs brand">
      <div class="brand-name">Delia's<br>Dog Grooming</div>
    </div>
    <div class="abs hero" role="img" aria-label="Photo of a schnauzer puppy sitting on a stone step beside the grass"></div>
    <div class="abs hero-caption">Lorem ipsum dolor sit amet, consectetuer adipiscing elit.<br>Nam nibh. Nunc varius facilisis eros.</div>
    <div class="abs hero-arrow" style="left:357px;top:145px"><svg width="8" height="10" viewBox="0 0 8 10"><path d="M5.5 1.5 2 5l3.5 3.5" stroke="#fff" stroke-width="1.8" fill="none"/></svg></div>
    <div class="abs hero-arrow" style="left:881px;top:145px"><svg width="8" height="10" viewBox="0 0 8 10"><path d="M2.5 1.5 6 5 2.5 8.5" stroke="#fff" stroke-width="1.8" fill="none"/></svg></div>
  </header>

  <nav class="abs nav">
    <div class="nav-item active" style="left:15px;width:85px">Home</div>
    <div class="nav-item" style="left:115px">About Us</div>
    <div class="nav-item" style="left:215px">Gallery</div>
    <div class="nav-item" style="left:306px">Online Store</div>
    <div class="nav-item" style="left:433px">Classes</div>
    <div class="nav-item" style="left:524px">Videos</div>
    <div class="nav-item" style="left:606px">Contact Us</div>
  </nav>

  <!-- appointment -->
  <section>
    <div class="abs panel" style="left:75px;top:370px;width:232px;height:357px"></div>
    <div class="abs panel-head" style="left:80px;top:375px;width:221px;height:39px;padding-left:28px">MAKE AN APPOINTMENT</div>
    <div class="abs field" style="top:430px">NAME</div>
    <div class="abs field" style="top:469px">EMAIL ADDRESS</div>
    <div class="abs field" style="top:507px">PHONE NUMBER</div>
    <div class="abs field" style="top:546px">WEIGHT, &amp; AGE<svg width="11" height="8" viewBox="0 0 11 8"><path d="M1.5 1.5 5.5 5.5 9.5 1.5" stroke="var(--purple)" stroke-width="2.2" fill="none"/></svg></div>
    <div class="abs field select" style="top:583px">BATH &amp; TRIM<svg width="11" height="8" viewBox="0 0 11 8"><path d="M1.5 1.5 5.5 5.5 9.5 1.5" stroke="var(--purple)" stroke-width="2.2" fill="none"/></svg></div>
    <div class="abs field select" style="top:621px;height:66px;line-height:normal;padding-top:29px">MESSAGE</div>
    <div class="abs submit">SUBMIT</div>
  </section>

  <!-- video -->
  <section>
    <div class="abs panel" style="left:75px;top:742px;width:232px;height:189px"></div>
    <div class="abs video" role="img" aria-label="Video still of a groomer clipping a black schnauzer"></div>
    <div class="abs video-title">Schnauzer Grooming</div>
    <div class="abs play"><svg width="34" height="24" viewBox="0 0 34 24"><path d="M13 6v12l10-6z" fill="#fff"/></svg></div>
  </section>

  <!-- services -->
  <section>
    <div class="abs panel" style="left:75px;top:945px;width:232px;height:154px"></div>
    <div class="abs panel-head" style="left:80px;top:950px;width:221px;height:36px;padding-left:24px">SERVICES</div>
    <ul class="abs services-list">
      <li><svg width="7" height="9" viewBox="0 0 7 9"><path d="M1.5 1 5 4.5 1.5 8" stroke="var(--purple)" stroke-width="2" fill="none"/></svg>Lorem ipsum dolor sit amet elit.</li>
      <li><svg width="7" height="9" viewBox="0 0 7 9"><path d="M1.5 1 5 4.5 1.5 8" stroke="var(--purple)" stroke-width="2" fill="none"/></svg>Lorem ipsum dolor sit amet elit.</li>
      <li><svg width="7" height="9" viewBox="0 0 7 9"><path d="M1.5 1 5 4.5 1.5 8" stroke="var(--purple)" stroke-width="2" fill="none"/></svg>Lorem ipsum dolor sit amet elit.</li>
      <li><svg width="7" height="9" viewBox="0 0 7 9"><path d="M1.5 1 5 4.5 1.5 8" stroke="var(--purple)" stroke-width="2" fill="none"/></svg>Lorem ipsum dolor sit amet elit.</li>
    </ul>
  </section>

  <!-- about -->
  <section>
    <h2 class="abs heading" style="left:346px;top:377px">About <b>ME</b></h2>
    <div class="abs portrait" role="img" aria-label="Portrait of Delia Okonkwo, arms crossed, in a dark jacket"></div>
    <div class="abs about-text">
      <p>Nunc varius facilisis eros. Sed erat. In in velit quis arcu ornare laoreet. Curabitur adipiscing luctus massa. Integer ut purus ac augue commodo commodo. Nunc nec mi eu justo tempor consectetuer. Etiam vitae nisl. In dignissim lacus ut ante. Cras elit lectus, bibendum a, adipiscing vitae, commodo et, dui.</p>
      <p style="margin-top:18.5px">Lorem ipsum dolor sit amet, consectetuer adipiscing elit. Nam nibh. Nunc varius facilisis eros. Sed erat. In in velit quis arcu ornare</p>
    </div>
    <div class="abs read-more">Read More &nbsp;&gt;&gt;</div>
  </section>

  <!-- before / after -->
  <section>
    <h2 class="abs heading" style="left:359px;top:629px"><b>Dog Grooming</b></h2>
    <div class="abs showcase" style="left:357px;top:667px;width:521px;height:201px"></div>
    <div class="abs shot" style="left:377px;top:686px;width:226px;height:143px;background:linear-gradient(160deg,#eeeeee 0%,#c9a27a 50%,#3a3a3a 100%)" role="img" aria-label="Long-haired dog before grooming"></div>
    <div class="abs shot" style="left:629px;top:686px;width:226px;height:143px;background:linear-gradient(160deg,#f4f4f4 0%,#d8c2a4 55%,#e9e9e9 100%)" role="img" aria-label="Same dog after grooming"></div>
    <div class="abs label" style="left:377px;top:840px">BEFORE</div>
    <div class="abs label" style="left:629px;top:840px">AFTER</div>

    <div class="abs showcase" style="left:357px;top:889px;width:521px;height:201px"></div>
    <div class="abs shot" style="left:377px;top:908px;width:226px;height:142px;background:linear-gradient(160deg,#dfe6ea 0%,#6f6a66 50%,#2c2c2c 100%)" role="img" aria-label="Shaggy schnauzer before grooming"></div>
    <div class="abs shot" style="left:629px;top:908px;width:226px;height:142px;background:linear-gradient(160deg,#e3eaee 0%,#8d8b88 50%,#3a3a3a 100%)" role="img" aria-label="Schnauzer after grooming with a neat trim"></div>
    <div class="abs label" style="left:377px;top:1062px">BEFORE</div>
    <div class="abs label" style="left:629px;top:1062px">AFTER</div>
  </section>

  <footer>
    <div class="abs social" style="left:78px"></div>
    <div class="abs social" style="left:113px"></div>
    <div class="abs social" style="left:149px"></div>
    <div class="abs social" style="left:185px"></div>
    <div class="abs social-name" style="left:71px">Chirply</div>
    <div class="abs social-name" style="left:106px">Friendnet</div>
    <div class="abs social-name" style="left:142px">Searcha</div>
    <div class="abs social-name" style="left:178px">ClipStream</div>
    <div class="abs footer-links">PRIVACY POLICY<span>|</span>DISCLAIMER<span>|</span>TERMS &amp; CONDITIONS<span>|</span>CONTACT US</div>
    <div class="abs copyright">© 2012 &nbsp;Delia's Dog Grooming, All Rights Reserved</div>
  </footer>
</div>
</body>
</html>
```